Business card for law firm

Need business card for new law firm. Think confident, authoritative, conservative, but not stuffy or old-fashioned.

Contact Information for Business Card

Content for card - logo (uploaded), plus the following:

Paul Whitcombe (larger font)
Managing Partner (larger font, but not as large as name)
Level 9, 7 Ferris Lane
Sydney NSW 2000
Main Tel 02 9364 2710
Direct Tel 02 8472 3159
Email paul@qvlegal.com.au
www.qvlegal.com.au

Letterhead design should include logo plus:
Level 9, 7 Ferris Lane
Sydney NSW 2000
Tel 02 8472 3159
www.qvlegal.com.au

```html
<!DOCTYPE html>
<html lang="en">
<head>
<meta charset="utf-8">
<title>Quayvale Legal – Letterhead</title>
<link href="https://fonts.googleapis.com/css2?family=Old+Standard+TT:wght@400&family=Questrial&display=swap" rel="stylesheet">
<style>
  :root {
    --backdrop: #e9e9e9;
    --paper-light: #f4f4f4;
    --paper-dark: #e2e2e2;
    --navy: #0d1f4f;
    --ink: #2a2a2a;
    --body-text: #6b6b6b;
    --salutation: #7a7a7a;
    --logo-grey: #6d6d6d;
    --signature-blue: #2d5aa8;
  }
  * { margin: 0; padding: 0; box-sizing: border-box; }
  html, body {
    width: 1024px;
    height: 1200px;
    overflow: hidden;
    background: var(--backdrop);
  }
  .letterhead {
    position: absolute;
    left: 98px;
    top: 20px;
    width: 828px;
    height: 1160px;
    background: linear-gradient(100deg, var(--paper-light) 0%, var(--paper-dark) 100%);
    border: 1px solid #d6d6d6;
  }
  .brand {
    position: absolute;
    left: 73px;
    top: 120px;
    display: flex;
    align-items: center;
    gap: 12px;
  }
  .brand-square {
    width: 22px;
    height: 22px;
    background: var(--navy);
  }
  .brand-name {
    font-family: "Old Standard TT", serif;
    font-size: 25px;
    font-weight: 400;
    letter-spacing: 1px;
    color: var(--logo-grey);
    text-transform: uppercase;
  }
  .contact-block {
    position: absolute;
    left: 603px;
    top: 82px;
    font-family: "Old Standard TT", serif;
    font-size: 15.5px;
    line-height: 18px;
    color: var(--ink);
  }
  .contact-block .address { margin-bottom: 7px; }
  .letter {
    position: absolute;
    left: 77px;
    top: 302px;
    width: 664px;
    font-family: "Questrial", sans-serif;
    color: var(--body-text);
  }
  .salutation {
    font-size: 21px;
    color: var(--salutation);
    margin-bottom: 36px;
  }
  .letter-body p {
    font-size: 12.6px;
    line-height: 15.6px;
    text-align: justify;
    margin-bottom: 15.6px;
  }
  .sign-off {
    font-size: 12.6px;
    margin-top: 34px;
  }
  .signature {
    position: absolute;
    left: 77px;
    top: 805px;
    width: 141px;
    height: 69px;
    background: linear-gradient(90deg, rgba(45,90,168,0.18), rgba(45,90,168,0.08));
    border-radius: 4px;
  }
  .footer-band {
    position: absolute;
    left: 0;
    bottom: 0;
    width: 100%;
    height: 17px;
    background: var(--navy);
  }
</style>
</head>
<body>
  <main class="letterhead">
    <div class="brand">
      <span class="brand-square"></span>
      <span class="brand-name">Quayvale Legal</span>
    </div>

    <address class="contact-block" style="font-style: normal;">
      <div class="address">Level 9, 7 Ferris Lane<br>Sydney NSW 2000</div>
      <div class="phone">02 8472 3159</div>
      <div class="web">www.qvlegal.com.au</div>
    </address>

    <section class="letter">
      <p class="salutation">Dear Mr. Carter,</p>
      <div class="letter-body">
        <p>Lorem ipsum dolor sit amet, consectetur adipiscing elit. Donec orci purus, luctus vitae dignissim eu, iaculis sed purus. Vivamus faucibus, ipsum nec aliquet viverra, leo mauris condimentum ligula, sit amet sagittis enim ligula quis arcu. Nam egestas tortor id nisi porttitor mattis. In tortor ante, ultricies in suscipit a, tempus non massa. Vivamus et auctor mi. Fusce vel massa nulla. Phasellus nec eros mauris, et scelerisque orci.</p>
        <p>Donec malesuada orci vitae nulla accumsan porta a id massa. Quisque accumsan iaculis magna sit amet fringilla. Maecenas consequat, magna eget tincidunt semper, odio nibh rutrum mi, id feugiat ante nisi eu risus. Vestibulum nunc orci, rhoncus a placerat in, ultricies in mi. Cras mattis varius eros, vel fringilla nisi suscipit eget. Quisque scelerisque sagittis nulla at porttitor.</p>
        <p>Sed id augue vitae urna euismod commodo aliquet a quam. Pellentesque arcu velit, cursus et malesuada ut, consequat et diam. Nullam erat sem, rhoncus id ullamcorper vitae, rhoncus et arcu. In ultricies ultricies nulla, ut rutrum nisi iaculis at. Donec eu magna a metus ornare faucibus. Fusce aliquet faucibus ultricies. Morbi semper, est id tincidunt gravida, sem arcu adipiscing lacus, ac bibendum nulla leo eu purus. Quisque nec diam sed risus consectetur accumsan quis quis nibh. Vestibulum id purus lorem.</p>
        <p>It is a long established fact that a reader will be distracted by the readable content of a page when looking at its layout. The point of using Lorem Ipsum is that it has a more-or-less normal distribution of letters, as opposed to using 'Content here, content here', making it look like readable English. Many desktop publishing packages</p>
      </div>
      <p class="sign-off">Sincerely,</p>
    </section>

    <div class="signature" role="img" aria-label="Handwritten signature of James Carter in blue ink"></div>

    <div class="footer-band"></div>
  </main>
</body>
</html>
```